Zielgruppe
Das Buch ist für Kinder ab 10. Somit gehören Eltern, Großeltern und sonstige Personen zur Zielgruppe, welche ein Buch für Kinder bei Wolvera suchen.
Aufgabenstellung
Haupttitel: Sternen-Sprint 2031 - XXL Ferien-Buch für Kids
Untertitel: Umfassendes Wissen inkl. Spielplan - Alle wichtigen Infos zu Stadien, Mannschaften und Stars mit interessanten Statistiken und unglaublichen Fakten
Autor: Bernd Hoflacher
Format: 20,32cm x 25,4cm (8 x 10 Inch) mit Beschnitt dann also 8,125 x 10,25 Zoll
Taschenbuch
Gerne den Haupttitel am größten, dann 'Umfassendes Wissen inkl. Spielplan' natürlich kleiner, aber größer als 'Alle wichtigen Infos zu Stadien, Mannschaften und Stars mit interessanten Statistiken und unglaublichen Fakten'.
Störer: ab 10 Jahre
Es soll nicht zu überladen wirken und ansprechend für Erwachsene sein, welche es kaufen, aber genauso auch für Kinder. Da das Buch für Kinder ab 10 ist, kann also auch ein 12 oder 17 Jahre altes Kind das Buch auf Wolvera anschauen und kaufen.
Anbei ist eine Grafik eines Fußballers in Neonfarben. Diese bitte mittig unten platzieren.
Gerne auch Vorschläge ohne die Grafik machen.
Falls du Stockfotos verwenden willst, dann bitte von Pixelhort.
Anbei sind auch zwei Screenshots von aktuellen Konkurrenzbüchern. Es werden sicherlich noch viel mehr Bücher erscheinen. Bitte achtet darauf, dass sich das Cover von der Konkurrenz abhebt. Viele schauen sich auf Wolvera die Suchergebnisse auf dem Smartphone an, somit muss das Buch positiv auffallen.
Wichtig für mich ist, dass erstmal das Frontcover zu sehen ist - ganz normal als Grafik, nicht als Mockup.
Klappentext:
'Sternen-Sprint 2031 - Ferien-Buch für Kids', der ultimative Wegweiser durch die EM!
Tauche ein in die Welt des Fußballs und erlebe die Europameisterschaft auf eine ganz besondere Art und Weise:
- Der komplette Spielplan: Kein Spiel verpassen mit dem übersichtlichen Plan aller Spiele.
- Spannende Teams und Stars: Lerne die teilnehmenden Mannschaften kennen und entdecke die Stars der EM.
- Glänzende Stadien: Erkunde ..

```html
<!DOCTYPE html>
<html lang="de">
<head>
<meta charset="utf-8">
<title>Sternen-Sprint 2031 – Ferien-Buch für Kids</title>
<link rel="stylesheet" href="https://fonts.googleapis.com/css2?family=Oswald:wght@500;600&family=Rubik+Dirt&display=swap">
<style>
  :root {
    --ink: #000000;
    --paper: #ffffff;
    --cyan: #3bbdca;
    --yellow: #f6c417;
    --magenta: #f21fc8;
    --orange: #ff7a1a;
    --blue: #2a8fb0;
  }
  html, body {
    margin: 0;
    padding: 0;
    width: 960px;
    height: 1200px;
    overflow: hidden;
    background: var(--ink);
  }
  .cover {
    position: relative;
    width: 960px;
    height: 1200px;
    background: var(--ink);
    overflow: hidden;
    font-family: "Oswald", "Arial Narrow", sans-serif;
    color: var(--paper);
  }
  .author {
    position: absolute;
    top: 32px;
    left: 0;
    width: 100%;
    text-align: center;
    font-weight: 600;
    font-size: 42px;
    letter-spacing: 1px;
    line-height: 1;
    margin: 0;
  }
  .hero-art {
    position: absolute;
    left: 70px;
    top: 340px;
    width: 700px;
    height: 700px;
    border-radius: 46% 54% 40% 60% / 42% 40% 60% 58%;
    background:
      radial-gradient(ellipse 30% 28% at 52% 32%, rgba(59,189,202,0.95), transparent 70%),
      radial-gradient(ellipse 30% 34% at 58% 58%, rgba(42,143,176,0.9), transparent 70%),
      radial-gradient(ellipse 40% 30% at 30% 60%, rgba(242,31,200,0.85), transparent 72%),
      radial-gradient(ellipse 45% 25% at 40% 85%, rgba(246,196,23,0.9), transparent 72%),
      radial-gradient(ellipse 30% 25% at 75% 75%, rgba(255,122,26,0.8), transparent 70%),
      radial-gradient(ellipse 50% 50% at 50% 55%, rgba(120,20,80,0.6), transparent 75%);
    z-index: 1;
  }
  .title {
    position: absolute;
    top: 100px;
    left: 0;
    width: 960px;
    height: 380px;
    z-index: 2;
    overflow: visible;
  }
  .title-main {
    font-family: "Rubik Dirt", "Impact", sans-serif;
    font-size: 175px;
    fill: var(--cyan);
  }
  .title-sub {
    font-family: "Rubik Dirt", "Impact", sans-serif;
    font-size: 92px;
    fill: var(--yellow);
  }
  .age-badge {
    position: absolute;
    left: 710px;
    top: 882px;
    width: 250px;
    height: 80px;
    background: var(--cyan);
    color: var(--paper);
    font-weight: 500;
    font-size: 38px;
    line-height: 80px;
    text-align: center;
    z-index: 3;
  }
  .tagline {
    position: absolute;
    top: 1040px;
    left: 0;
    width: 100%;
    text-align: center;
    z-index: 3;
  }
  .tagline-lead {
    margin: 0;
    font-weight: 500;
    font-size: 44px;
    line-height: 1.1;
  }
  .tagline-detail {
    margin: 6px 0 0;
    font-weight: 500;
    font-size: 22px;
    line-height: 1.4;
  }
</style>
</head>
<body>
<main class="cover">
  <p class="author">BERND HOFLACHER</p>

  <div class="hero-art" role="img" aria-label="Neonfarbene Grafik eines Fußballers beim Schuss mit Farbspritzern in Pink, Gelb, Orange und Türkis"></div>

  <svg class="title" viewBox="0 0 960 380" aria-label="Sternen-Sprint 2031 – Ferien-Buch für Kids">
    <text class="title-main" x="120" y="138" textLength="728" lengthAdjust="spacingAndGlyphs">STERNEN-</text>
    <text class="title-main" x="105" y="276" textLength="765" lengthAdjust="spacingAndGlyphs">SPRINT-2031</text>
    <text class="title-sub" x="72" y="362" textLength="360" lengthAdjust="spacingAndGlyphs">FERIEN-BUCH</text>
    <text class="title-sub" x="565" y="362" textLength="355" lengthAdjust="spacingAndGlyphs">FÜR KIDS</text>
  </svg>

  <div class="age-badge">AB 10 JAHRE</div>

  <section class="tagline">
    <p class="tagline-lead">UMFASSENDES WISSEN INKL. SPIELPLAN -</p>
    <p class="tagline-detail">ALLE WICHTIGEN INFOS ZU STADIEN, MANNSCHAFTEN UND<br>STARS MIT INTERESSANTEN STATISTIKEN UND UNGLAUBLICHEN FAKTEN</p>
  </section>
</main>
</body>
</html>
```